furniture and home contents restoration

I need to list the services that we perform in our studio.
we serve the general public as well as the insurance/ remediation industry

```html
<!DOCTYPE html>
<html lang="en">
<head>
<meta charset="utf-8">
<title>Ashcombe Studio – Business Card</title>
<link href="https://fonts.googleapis.com/css2?family=Noto+Serif:wght@400;700&display=swap" rel="stylesheet">
<style>
  :root{
    --stage:#e9e7e4;
    --slate:#1f3440;
    --ink:#1c2e3a;
    --paper:#ffffff;
    --on-slate:#eef2f4;
  }
  *{margin:0;padding:0;box-sizing:border-box}
  html,body{width:1200px;height:930px;overflow:hidden}
  body{
    background:var(--stage);
    font-family:"Noto Serif",Georgia,serif;
    display:flex;flex-direction:column;align-items:center;justify-content:center;gap:40px;
  }
  .card{
    width:700px;height:400px;border-radius:18px;position:relative;overflow:hidden;
    box-shadow:0 6px 18px rgba(0,0,0,.18);
  }
  /* Back side */
  .card--back{background:var(--slate);color:var(--on-slate);padding:32px 34px 0}
  .back__title{
    text-align:center;font-weight:700;font-size:30px;letter-spacing:.5px;color:#fff;
  }
  .services{display:flex;gap:18px;margin-top:16px}
  .services ul{list-style:none;flex:1}
  .services li{
    font-size:11.5px;line-height:19px;text-transform:uppercase;letter-spacing:.2px;white-space:nowrap;
  }
  .services li::before{content:"•";margin-right:6px}
  .back__footer{
    position:absolute;left:0;right:0;bottom:32px;text-align:center;
    font-size:15.5px;line-height:22px;text-transform:uppercase;letter-spacing:.3px;
  }
  /* Front side */
  .card--front{background:var(--paper);color:var(--ink)}
  .front__tagline{
    position:absolute;left:390px;top:36px;width:280px;font-size:15px;line-height:19px;
  }
  .front__company{
    position:absolute;left:44px;top:120px;font-weight:700;font-size:36px;line-height:38px;letter-spacing:.5px;
  }
  .contacts{
    position:absolute;left:390px;top:180px;list-style:none;font-size:15px;line-height:21px;
  }
  .contacts li{display:flex;align-items:center;gap:8px}
  .contacts svg{width:12px;height:12px;flex:none}
  .front__specialty{
    position:absolute;left:390px;top:296px;font-size:16px;text-transform:uppercase;letter-spacing:.3px;
  }
  .front__person{
    position:absolute;left:44px;bottom:34px;font-weight:700;font-size:27px;letter-spacing:.5px;
  }
  .front__marker{
    position:absolute;left:0;bottom:40px;width:18px;height:22px;background:var(--slate);
  }
</style>
</head>
<body>

<section class="card card--back" aria-label="Card back: services">
  <h1 class="back__title">ASHCOMBE STUDIO</h1>
  <div class="services">
    <ul>
      <li>Antique repair and restoration</li>
      <li>Art cleaning and remounting</li>
      <li>Art and mirror frame repair</li>
      <li>Chandelier cleaning and restoration</li>
      <li>Document restoration</li>
      <li>Glass, ceramic, and mirror repair</li>
      <li>Hardware repair and restoration</li>
      <li>Kitchen removal and reinstallation</li>
      <li>Lamp cleaning and restoration</li>
      <li>Lamp shade replacement</li>
    </ul>
    <ul>
      <li>Metal polishing and restoration</li>
      <li>Odor removal and ozone services</li>
      <li>Photo restoration</li>
      <li>Upholstery cleaning and deodorizing</li>
      <li>In-house upholstery and reupholstery</li>
      <li>Rug cleaning and restoration</li>
      <li>Musical instrument restoration</li>
      <li>Window treatment repair/ restoration</li>
      <li>Leather restoration and replacement</li>
      <li>Piano restoration and repair</li>
    </ul>
  </div>
  <p class="back__footer">On-site inspections and desk review services<br>Assessment reports and estimates for repair and restoration</p>
</section>

<section class="card card--front" aria-label="Card front: contact">
  <p class="front__tagline">serving the general public and the insurance industry for over 40 years</p>
  <h2 class="front__company">ASHCOMBE<br>STUDIO</h2>
  <ul class="contacts">
    <li><svg viewBox="0 0 12 12"><path d="M2.5 1l2 2.3-1 1.3a7 7 0 0 0 3.9 3.9l1.3-1 2.3 2-1 1.5C6 11 1 6 1 2z" fill="var(--ink)"/></svg>555 210 4400</li>
    <li><svg viewBox="0 0 12 12"><rect x="3" y="0.8" width="6" height="10.4" rx="1" fill="none" stroke="var(--ink)" stroke-width="1.2"/><rect x="5.2" y="9" width="1.6" height="1" fill="var(--ink)"/></svg>555 318 7624</li>
    <li><svg viewBox="0 0 12 12"><rect x="3" y="1" width="6" height="3" fill="none" stroke="var(--ink)" stroke-width="1"/><rect x="1" y="4" width="10" height="5" rx="1" fill="var(--ink)"/><rect x="3" y="8" width="6" height="3" fill="#fff" stroke="var(--ink)" stroke-width="1"/></svg>555 210 4460</li>
    <li><svg viewBox="0 0 12 12"><path d="M6 11.5S2 7 2 4.5a4 4 0 0 1 8 0C10 7 6 11.5 6 11.5z" fill="var(--ink)"/><circle cx="6" cy="4.5" r="1.4" fill="#fff"/></svg>12 elm brook rd. ashford, ny 10500</li>
    <li><svg viewBox="0 0 12 12"><rect x="1" y="2.5" width="10" height="7" fill="none" stroke="var(--ink)" stroke-width="1.1"/><path d="M1 2.5l5 4 5-4" fill="none" stroke="var(--ink)" stroke-width="1.1"/></svg>hello@ashcombestudio.com</li>
  </ul>
  <p class="front__specialty">Home contents restoration</p>
  <span class="front__marker"></span>
  <p class="front__person">DANIEL MORETTI</p>
</section>

</body>
</html>
```